Poster for a online company that buys your stuff

SwapKestrel offers a website which customers can get a instant offer for stuff their looking to sell. They then Courier the items in to us and they get paid the same day it arrives
We're looking for an eye catching design which portrays our hassle free process
We'll need your help to come up with a slogan/catch phrase and our easy 1,2,3 process so customers can see the poster and instantly have a clear understanding of what we do
1. Get an instant offer on our website
2. Send your item(s) to us
3.Get paid within 24 Hours
Industry/Entity Type
It Company
Look and feel
Each slider illustrates characteristics of the customer's brand and the style your logo design should communicate.

```html
<!DOCTYPE html>
<html lang="en">
<head>
<meta charset="utf-8">
<title>SwapKestrel – How It Works</title>
<link href="https://fonts.googleapis.com/css2?family=Roboto:wght@500;700&family=Teko:wght@500&family=Lobster&display=swap" rel="stylesheet">
<style>
  :root {
    --backdrop: #1f0d0e;
    --sheet-title: #8b8282;
    --panel: #ffffff;
    --green: #8dc63f;
    --ring: #ffffff;
    --text: #2f2f2f;
    --heading: #222222;
  }
  * { box-sizing: border-box; margin: 0; padding: 0; }
  html, body { width: 1200px; height: 1200px; overflow: hidden; }
  body {
    background: var(--backdrop);
    font-family: "Roboto", Arial, sans-serif;
    position: relative;
  }
  .sheet-title {
    position: absolute; top: 38px; left: 0; width: 100%;
    text-align: center; color: var(--sheet-title);
    font-size: 42px; font-weight: 500; letter-spacing: 1px;
  }
  .panel {
    position: absolute; width: 565px; height: 282px;
    background: var(--panel);
  }
  .panel--tl { left: 14px; top: 269px; }
  .panel--tr { left: 621px; top: 269px; }
  .panel--bl { left: 14px; top: 656px; }
  .panel--br { left: 621px; top: 656px; }
  .panel--dark { --ink: #111111; }
  .panel--light { --ink: #ffffff; }

  .panel-header {
    position: absolute; top: 6px; left: 0; width: 100%;
    display: flex; justify-content: center; align-items: flex-end; gap: 6px;
  }
  .headline {
    color: var(--heading);
    border-bottom: 1.5px solid var(--heading);
    line-height: 1;
    font-weight: 400;
  }
  .headline--block {
    font-family: "Teko", "Oswald", sans-serif; font-weight: 500;
    font-size: 40px; padding-top: 4px; margin-left: 60px;
  }
  .headline--script {
    font-family: "Lobster", cursive; font-size: 33px; padding: 2px 0 1px;
    margin-left: 40px;
  }
  .brand-mark {
    display: flex; align-items: center; gap: 3px;
    font-size: 8px; font-weight: 700; color: var(--heading);
    padding-bottom: 2px;
  }
  .brand-mark__dot {
    width: 7px; height: 7px; border-radius: 50%; background: var(--green);
  }

  .step {
    position: absolute; top: 63px; width: 180px; margin-left: -90px;
    display: flex; flex-direction: column; align-items: center;
  }
  .step--one { left: 101px; }
  .step--two { left: 281px; }
  .step--three { left: 474px; }
  .step__pill {
    background: var(--green); color: #fff;
    font-size: 16px; font-weight: 500;
    width: 86px; height: 27px; border-radius: 14px;
    display: flex; align-items: center; justify-content: center;
  }
  .step__badge {
    margin-top: 14px; width: 116px; height: 116px; border-radius: 50%;
    background: var(--green); border: 4px solid var(--ring);
    box-shadow: 0 1px 5px rgba(0,0,0,0.35);
    display: flex; align-items: center; justify-content: center;
  }
  .step__badge svg { width: 70px; height: 70px; }
  .icon-ink { fill: var(--ink); }
  .icon-stroke { stroke: var(--ink); fill: none; }
  .figure-slot {
    width: 66px; height: 66px; border-radius: 8px;
    background: var(--ink); opacity: 0.9;
  }
  .step__label {
    margin-top: 14px; text-align: center; color: var(--text);
    font-size: 16px; font-weight: 500; line-height: 20px;
  }
</style>
</head>
<body>
  <h1 class="sheet-title">SUBMISSION IDEAS - 01</h1>

  <svg width="0" height="0" style="position:absolute">
    <defs>
      <g id="cart-icon">
        <path class="icon-stroke" d="M4 10 H12 L18 40" stroke-width="5" stroke-linecap="round" stroke-linejoin="round"/>
        <path class="icon-ink" d="M12 18 H46 L40 42 H18 Z"/>
        <circle class="icon-ink" cx="22" cy="54" r="5"/>
        <circle class="icon-ink" cx="38" cy="54" r="5"/>
        <circle class="icon-ink" cx="50" cy="18" r="13"/>
        <path d="M44 18 L49 23 L57 13" stroke="#8dc63f" stroke-width="3.5" fill="none" stroke-linecap="round" stroke-linejoin="round"/>
      </g>
      <g id="laptop-icon">
        <path class="icon-stroke" d="M34 22 H10 V49 H52 V38" stroke-width="4" stroke-linejoin="miter"/>
        <path class="icon-ink" d="M2 52 H62 L57 58 H7 Z"/>
        <rect x="27" y="53" width="10" height="2" fill="#8dc63f"/>
        <rect class="icon-ink" x="50" y="4" width="10" height="10"/>
        <rect class="icon-ink" x="42" y="12" width="8" height="8"/>
        <rect class="icon-ink" x="52" y="20" width="7" height="7"/>
        <rect class="icon-ink" x="37" y="24" width="7" height="7"/>
        <rect class="icon-ink" x="44" y="30" width="6" height="6"/>
        <rect class="icon-ink" x="30" y="34" width="6" height="6"/>
        <rect class="icon-ink" x="38" y="38" width="5" height="5"/>
        <rect class="icon-ink" x="22" y="39" width="5" height="5"/>
        <rect class="icon-ink" x="30" y="42" width="4" height="4"/>
        <rect class="icon-ink" x="16" y="42" width="4" height="4"/>
      </g>
    </defs>
  </svg>

  <section class="panel panel--tl panel--dark">
    <header class="panel-header">
      <h2 class="headline headline--block">HOW IT WORKS?</h2>
      <span class="brand-mark"><span class="brand-mark__dot"></span>SwapKestrel</span>
    </header>
    <div class="step step--one">
      <div class="step__pill">Step 01</div>
      <div class="step__badge"><div class="figure-slot" role="img" aria-label="Pictogram of a person at a desk using a laptop"></div></div>
      <p class="step__label">Get an instant offer<br>on our website</p>
    </div>
    <div class="step step--two">
      <div class="step__pill">Step 02</div>
      <div class="step__badge"><svg viewBox="0 0 64 64" aria-label="Shopping cart with tick"><use href="#cart-icon"/></svg></div>
      <p class="step__label">Send your item(s)<br>to us</p>
    </div>
    <div class="step step--three">
      <div class="step__pill">Step 03</div>
      <div class="step__badge"><div class="figure-slot" role="img" aria-label="Pictogram of a person at a desk receiving money"></div></div>
      <p class="step__label">Get paid within<br>24 Hours</p>
    </div>
  </section>

  <section class="panel panel--tr panel--light">
    <header class="panel-header">
      <h2 class="headline headline--script">Sell &amp; Get Paid Within 24 Hours</h2>
      <span class="brand-mark"><span class="brand-mark__dot"></span>SwapKestrel</span>
    </header>
    <div class="step step--one">
      <div class="step__pill">Step 01</div>
      <div class="step__badge"><div class="figure-slot" role="img" aria-label="Pictogram of a person at a desk using a laptop"></div></div>
      <p class="step__label">Get an instant offer<br>on our website</p>
    </div>
    <div class="step step--two">
      <div class="step__pill">Step 02</div>
      <div class="step__badge"><svg viewBox="0 0 64 64" aria-label="Shopping cart with tick"><use href="#cart-icon"/></svg></div>
      <p class="step__label">Send your item(s)<br>to us</p>
    </div>
    <div class="step step--three">
      <div class="step__pill">Step 03</div>
      <div class="step__badge"><div class="figure-slot" role="img" aria-label="Pictogram of a person at a desk receiving money"></div></div>
      <p class="step__label">Get paid within<br>24 Hours</p>
    </div>
  </section>

  <section class="panel panel--bl panel--light">
    <header class="panel-header">
      <h2 class="headline headline--block">HOW IT WORKS?</h2>
      <span class="brand-mark"><span class="brand-mark__dot"></span>SwapKestrel</span>
    </header>
    <div class="step step--one">
      <div class="step__pill">Step 01</div>
      <div class="step__badge"><svg viewBox="0 0 64 64" aria-label="Laptop with digital squares"><use href="#laptop-icon"/></svg></div>
      <p class="step__label">Get an instant offer<br>on our website</p>
    </div>
    <div class="step step--two">
      <div class="step__pill">Step 02</div>
      <div class="step__badge"><svg viewBox="0 0 64 64" aria-label="Shopping cart with tick"><use href="#cart-icon"/></svg></div>
      <p class="step__label">Send your item(s)<br>to us</p>
    </div>
    <div class="step step--three">
      <div class="step__pill">Step 03</div>
      <div class="step__badge"><div class="figure-slot" role="img" aria-label="Pictogram of a person at a desk receiving money"></div></div>
      <p class="step__label">Get paid within<br>24 Hours</p>
    </div>
  </section>

  <section class="panel panel--br panel--dark">
    <header class="panel-header">
      <h2 class="headline headline--script">Sell &amp; Get Paid Within 24 Hours</h2>
      <span class="brand-mark"><span class="brand-mark__dot"></span>SwapKestrel</span>
    </header>
    <div class="step step--one">
      <div class="step__pill">Step 01</div>
      <div class="step__badge"><svg viewBox="0 0 64 64" aria-label="Laptop with digital squares"><use href="#laptop-icon"/></svg></div>
      <p class="step__label">Get an instant offer<br>on our website</p>
    </div>
    <div class="step step--two">
      <div class="step__pill">Step 02</div>
      <div class="step__badge"><svg viewBox="0 0 64 64" aria-label="Shopping cart with tick"><use href="#cart-icon"/></svg></div>
      <p class="step__label">Send your item(s)<br>to us</p>
    </div>
    <div class="step step--three">
      <div class="step__pill">Step 03</div>
      <div class="step__badge"><div class="figure-slot" role="img" aria-label="Pictogram of a person at a desk receiving money"></div></div>
      <p class="step__label">Get paid within<br>24 Hours</p>
    </div>
  </section>
</body>
</html>
```